Nordlys Boligforum

Company is in: Denmark - Copenhagen
It sells: Restaurants and café buildings
Companys age: 25 years
Main benefit: trust with over 25 years experience

```html
<!DOCTYPE html>
<html lang="en">
<head>
<meta charset="utf-8">
<title>Nordlys Boligforum</title>
<link rel="stylesheet" href="https://fonts.googleapis.com/css2?family=Arimo:ital,wght@0,400;0,700;1,400&display=swap">
<style>
  :root {
    --page-deep: #062b45;
    --page-mid: #0b4870;
    --nav-bg: #05283d;
    --nav-active: #0a4a72;
    --nav-line: #1b5577;
    --slider-frame: #0d6299;
    --welcome-bg: #f8f0e1;
    --content-bg: #fdfbf7;
    --heading-blue: #0b3d5c;
    --heading-red: #9e1b0e;
    --body-text: #1e1e1e;
    --link-blue: #2a6aa0;
    --white: #ffffff;
  }
  * { box-sizing: border-box; margin: 0; padding: 0; }
  html, body { width: 1200px; height: 1055px; overflow: hidden; }
  body {
    position: relative;
    font-family: "Arimo", Arial, sans-serif;
    background: radial-gradient(ellipse at 50% 10%, var(--page-mid) 0%, var(--page-deep) 75%);
  }
  .brand {
    position: absolute; left: 131px; top: 60px;
    color: var(--white); font-size: 26px; font-weight: 700; letter-spacing: 0.5px;
  }
  .main-nav {
    position: absolute; left: 0; top: 110px; width: 1200px; height: 55px;
    background: var(--nav-bg);
  }
  .main-nav ul { list-style: none; position: absolute; left: 120px; top: 5px; display: flex; height: 45px; }
  .main-nav li {
    display: flex; align-items: center; justify-content: center;
    color: var(--white); font-size: 18px; font-weight: 700;
    border-right: 1px solid var(--nav-line);
  }
  .main-nav li:last-child { border-right: none; }
  .main-nav li.is-active {
    background: linear-gradient(var(--nav-active), #073652);
    border-left: 1px solid var(--nav-line);
  }
  .page-panel {
    position: absolute; left: 130px; top: 175px; width: 940px; height: 805px;
    background: var(--content-bg);
    box-shadow: 0 4px 8px rgba(0,0,0,0.45);
  }
  .slider {
    position: absolute; left: 0; top: 0; width: 940px; height: 298px;
    background: var(--slider-frame);
  }
  .slide-photo {
    position: absolute; left: 12px; top: 10px; width: 918px; height: 280px;
    background: linear-gradient(90deg, #c9a374 0%, #8a6a45 30%, #3d2a1c 50%, #6c4a30 70%, #2c2018 100%);
  }
  .slider-arrow { position: absolute; top: 133px; }
  .slider-arrow.prev { left: 22px; }
  .slider-arrow.next { left: 895px; }
  .slider-pager { position: absolute; left: 800px; top: 260px; display: flex; gap: 1px; }
  .slider-pager span {
    width: 20px; height: 19px; display: flex; align-items: center; justify-content: center;
    font-size: 13px; background: #d6d6d6; color: #111;
  }
  .slider-pager span.is-current { background: var(--heading-blue); color: var(--white); }
  .welcome {
    position: absolute; left: 0; top: 298px; width: 940px; height: 187px;
    background: var(--welcome-bg); padding: 16px 30px 0 35px;
  }
  .welcome h1 { font-size: 25px; color: var(--heading-blue); font-weight: 700; margin-bottom: 4px; }
  .welcome p { font-size: 16px; line-height: 25px; color: var(--body-text); }
  .features { position: absolute; left: 0; top: 485px; width: 940px; height: 320px; }
  .feature { position: absolute; top: 10px; width: 260px; }
  .feature h2 { font-size: 25px; color: var(--heading-red); font-weight: 700; margin-bottom: 12px; }
  .feature-photo {
    width: 255px; height: 130px; border: 5px solid var(--white);
    box-shadow: 0 1px 4px rgba(0,0,0,0.35); margin-bottom: 10px;
  }
  .feature p { font-size: 14px; line-height: 21px; color: #000; }
  .feature a { font-size: 14px; line-height: 25px; font-style: italic; color: var(--link-blue); text-decoration: underline; }
  .feature-divider {
    position: absolute; top: 40px; width: 1px; height: 230px;
    background: linear-gradient(transparent, #e8e1d4, transparent);
  }
  .copyright {
    position: absolute; right: 131px; top: 1004px;
    font-size: 12px; color: var(--white);
  }
</style>
</head>
<body>
  <div class="brand">NORDLYS BOLIGFORUM</div>

  <nav class="main-nav">
    <ul>
      <li style="width:120px">Home</li>
      <li class="is-active" style="width:146px">For Sale</li>
      <li style="width:215px">Links/Download</li>
      <li style="width:160px">Newsletter</li>
      <li style="width:155px">About Us</li>
      <li style="width:165px">Contact Us</li>
    </ul>
  </nav>

  <main class="page-panel">
    <section class="slider">
      <div class="slide-photo" role="img" aria-label="Elegant restaurant dining room with columns, curtains and an open kitchen"></div>
      <svg class="slider-arrow prev" width="24" height="40" viewBox="0 0 24 40"><path d="M18 2 L6 20 L18 38" fill="none" stroke="#d8d8d8" stroke-width="6"/></svg>
      <svg class="slider-arrow next" width="24" height="40" viewBox="0 0 24 40"><path d="M6 2 L18 20 L6 38" fill="none" stroke="#d8d8d8" stroke-width="6"/></svg>
      <div class="slider-pager">
        <span class="is-current">1</span><span>2</span><span>3</span><span>4</span><span>5</span><span>6</span>
      </div>
    </section>

    <section class="welcome">
      <h1>Welcome to NORDLYS BOLIGFORUM</h1>
      <p>Lorem ipsum dolor sit amet, consectetuer adipiscing elit. Aenean commodo ligula eget dolor. Aenean massa. Cum sociis natoque penatibus et magnis dis parturient montes, nascetur ridiculus mus. Donec quam felis, ultricies nec, pellentesque eu, pretium quis, sem. Nulla consequat massa quis enim. Donec pede justo, fringilla vel, aliquet nec, vulputate eget, arcu. In enim justo, rhoncus ut, imperdiet a, venenatis vitae, justo. Nullam dictum felis eu pede mollis pretium. Integer tincidunt. Cras dapibus. Vivamus elementum semper nisi.</p>
    </section>

    <section class="features">
      <article class="feature" style="left:35px">
        <h2>Restaurant</h2>
        <div class="feature-photo" role="img" aria-label="Restaurant dining hall with violet lit walls and white chairs" style="background:linear-gradient(#9a72c6,#5a3a70 55%,#a07850)"></div>
        <p>Lorem ipsum dolor sit amet, con-sectetuer adipiscing elit. Aenean com-modo ligula eget dolor.</p>
        <a href="#">Read more...</a>
      </article>
      <div class="feature-divider" style="left:315px"></div>
      <article class="feature" style="left:345px">
        <h2>Cafe</h2>
        <div class="feature-photo" role="img" aria-label="Cafe table set with glasses, flowers and a teapot" style="background:linear-gradient(135deg,#c8a050,#8a5a20 60%,#e8dcc8)"></div>
        <p>Lorem ipsum dolor sit amet, con-sectetuer adipiscing elit. Aenean com-modo ligula eget dolor.</p>
        <a href="#">Read more...</a>
      </article>
      <div class="feature-divider" style="left:625px"></div>
      <article class="feature" style="left:655px">
        <h2>Pab</h2>
        <div class="feature-photo" role="img" aria-label="Brick corner pub building with flower boxes" style="background:linear-gradient(#8a6a58,#5a3a30 60%,#2a2a2a)"></div>
        <p>Lorem ipsum dolor sit amet, con-sectetuer adipiscing elit. Aenean com-modo ligula eget dolor.</p>
        <a href="#">Read more...</a>
      </article>
    </section>
  </main>

  <footer class="copyright">Copyright © 2011 NORDLYS BOLIGFORUM All rights reserved</footer>
</body>
</html>
```